Redesign of business card for Cedar Ridge Mechanical

We are looking for a new design for our business cards for Cedar Ridge Mechanical. We are a plumbing & HVAC construction company, operating on the West Coast of Canada and USA. Logo attached.
Industry/Entity Type
Construction - Plumbing & HVAC
Contact Information for Business Card
Name, address, phone numbers, email, website address
Look and feel
Each slider illustrates characteristics of the customer's brand and the style your logo design should communicate.

```html
<!DOCTYPE html>
<html lang="en">
<head>
<meta charset="utf-8">
<title>Cedar Ridge Mechanical – Business Card</title>
<link href="https://fonts.googleapis.com/css2?family=Mulish:wght@400;700;800&display=swap" rel="stylesheet">
<style>
  :root {
    --bg: #d6d6d6;
    --ink: #050505;
    --paper: #ffffff;
    --steel: #8e9090;
    --shadow: rgba(0,0,0,0.28);
  }
  html, body {
    margin: 0;
    width: 1200px;
    height: 896px;
    overflow: hidden;
    background: var(--bg);
    font-family: "Mulish", sans-serif;
  }
  .card {
    position: absolute;
    left: 334px;
    width: 528px;
    height: 302px;
    border-radius: 20px;
    overflow: hidden;
    box-shadow: 0 10px 22px var(--shadow);
  }
  .card-back {
    top: 125px;
    background: var(--ink);
  }
  .card-back .pattern-area {
    position: absolute;
    inset: 0;
    background: linear-gradient(120deg, #5a5a5a 0%, #2a2a2a 35%, #0b0b0b 60%, #050505 100%);
  }
  .card-front {
    top: 474px;
    background: var(--paper);
  }
  .wave {
    position: absolute;
    inset: 0;
    width: 528px;
    height: 302px;
  }
  .brand {
    position: absolute;
    left: 20px;
    top: 24px;
    display: flex;
    align-items: flex-start;
    gap: 10px;
  }
  .brand-mark {
    width: 22px;
    height: 22px;
    background: var(--ink);
    margin-top: 3px;
  }
  .brand-name {
    font-weight: 800;
    font-size: 24px;
    line-height: 1.08;
    color: var(--ink);
    letter-spacing: 0.5px;
  }
  .contact {
    position: absolute;
    right: 19px;
    top: 108px;
    text-align: right;
    color: var(--paper);
  }
  .person-name {
    font-weight: 700;
    font-size: 19px;
    letter-spacing: 0.6px;
    margin: 0;
  }
  .person-title {
    font-size: 13.5px;
    margin: 4px 0 0;
  }
  .address {
    font-size: 13.5px;
    line-height: 21px;
    margin: 14px 0 0;
  }
  .lines {
    list-style: none;
    margin: 12px 0 0;
    padding: 0;
    font-size: 13.5px;
    line-height: 21px;
  }
  .lines li {
    display: flex;
    justify-content: flex-end;
    align-items: center;
    gap: 7px;
  }
  .lines svg {
    width: 11px;
    height: 11px;
    fill: var(--paper);
  }
</style>
</head>
<body>

<div class="card card-back">
  <div class="pattern-area" role="img" aria-label="Repeating company monogram pattern in glossy black"></div>
</div>

<div class="card card-front">
  <svg class="wave" viewBox="0 0 897 514" preserveAspectRatio="none" aria-hidden="true">
    <path d="M0,352 C300,346 520,110 897,38 L897,514 L0,514 Z" fill="var(--ink)"/>
    <path d="M0,378 C200,376 360,330 470,262 C380,336 210,420 0,440 Z" fill="var(--steel)"/>
    <path d="M0,378 C300,372 480,230 620,155 C720,105 820,100 897,100" fill="none" stroke="var(--paper)" stroke-width="7"/>
    <path d="M0,448 C220,442 370,370 470,275" fill="none" stroke="var(--paper)" stroke-width="6"/>
  </svg>

  <div class="brand">
    <div class="brand-mark"></div>
    <div class="brand-name">CEDAR RIDGE<br>MECHANICAL</div>
  </div>

  <div class="contact">
    <p class="person-name">DANIEL HARTLEY</p>
    <p class="person-title">Managing Director</p>
    <p class="address">Your address, City<br>State, Zip 1234</p>
    <ul class="lines">
      <li>123 456 789
        <svg viewBox="0 0 24 24"><path d="M6.6 10.8a15 15 0 0 0 6.6 6.6l2.2-2.2a1 1 0 0 1 1-.25 11.4 11.4 0 0 0 3.6.57 1 1 0 0 1 1 1V20a1 1 0 0 1-1 1A17 17 0 0 1 3 4a1 1 0 0 1 1-1h3.5a1 1 0 0 1 1 1c0 1.25.2 2.45.57 3.57a1 1 0 0 1-.25 1z"/></svg>
      </li>
      <li>info@yourmail.com
        <svg viewBox="0 0 24 24"><path d="M2 6h20v12H2z M2 6l10 7 10-7" stroke="#000" stroke-width="1.5"/></svg>
      </li>
      <li>www.yourwebsite.com
        <svg viewBox="0 0 24 24"><circle cx="12" cy="12" r="10"/></svg>
      </li>
    </ul>
  </div>
</div>

</body>
</html>
```